Quick Straightforward Billboard Redesign

- Design billboard sized for 10 foot' x 36' foot width live area size and please include bleeds 6" around all sides
- Exact blue color match is imperative in headline, logo, phone number bubble or wherever used. C-83 / M-45 / Y-1 / K-0-
- What I hope to illustrate is that our company offers the best porch screening in the area area, in regards to quality, expertise, durability, storms proof, but we do not build screen porches.
- Current board is attached below from previous designer, and as you can see sizing was off, white space on edges make it appear to be sized incorrectly.
- I also attached my own little mock up idea well well if it helps, favorite image, logo, headline, etc and ideas perhaps on expanding or making this better?

Thanks so much!

Target Market(s)

Drivers and passengers, Southeastern NC, are of immense new construction and high end homes.

Industry/Entity Type

Construction

Colors
0054AA
0677BA
7BADD7
CADEEF
E8F1F8

Requirements
Must have
• Blue color matching
Nice to have
• Design spins or other thoughts on my little mock up

```html
<!DOCTYPE html>
<html lang="en">
<head>
<meta charset="utf-8">
<title>Harborline Porchworks Billboard</title>
<link rel="stylesheet" href="https://fonts.googleapis.com/css2?family=Barlow+Condensed:wght@600&family=Lexend:wght@400&display=swap">
<style>
  :root {
    --page-bg: #f1f1f1;
    --brand-deep: #0a62b8;
    --brand-mid: #0677ba;
    --brand-light: #14aae0;
    --call-green: #00b050;
    --white: #ffffff;
    --photo-sky: #cfe3f3;
    --photo-ceiling: #eef0f1;
    --photo-lawn: #7fa25a;
    --photo-deck: #b7aa98;
  }
  * { margin: 0; padding: 0; box-sizing: border-box; }
  html, body {
    width: 1200px; height: 1159px; overflow: hidden;
    background: var(--page-bg);
  }
  .billboard {
    position: absolute; left: 40px; top: 424px;
    width: 1120px; height: 311px;
    background: linear-gradient(90deg, var(--brand-deep) 0%, var(--brand-mid) 50%, var(--brand-light) 100%);
    color: var(--white);
    box-shadow: 0 18px 22px -14px rgba(0,0,0,.35);
  }
  .tagline {
    position: absolute; left: 50px; top: 47px;
    font: 400 16px/1 "Lexend", sans-serif; letter-spacing: -0.2px;
  }
  .headline {
    position: absolute; left: 48px; top: 74px;
    font: 600 70px/62px "Barlow Condensed", sans-serif; letter-spacing: -0.5px;
  }
  .brand {
    position: absolute; left: 50px; top: 226px;
    display: flex; align-items: center; gap: 12px;
    font: 600 42px/1 "Barlow Condensed", sans-serif; text-transform: uppercase;
  }
  .brand-mark { width: 40px; height: 40px; background: var(--white); }
  .distinction {
    position: absolute; right: 344px; top: 98px; width: 250px;
    text-align: right;
    font: 400 16px/22px "Lexend", sans-serif; letter-spacing: -0.2px;
  }
  .porch-photo {
    position: absolute; left: 799px; top: 33px; width: 277px; height: 246px;
    border: 2px solid var(--white);
    background: linear-gradient(180deg, var(--photo-ceiling) 0%, var(--photo-ceiling) 32%, var(--photo-sky) 42%, var(--photo-lawn) 55%, #8a7d6c 75%, var(--photo-deck) 100%);
  }
  .call-button {
    position: absolute; left: 583px; top: 218px; width: 301px; height: 63px;
    background: var(--call-green);
    display: flex; align-items: center; justify-content: center; gap: 10px;
    font: 600 54px/1 "Barlow Condensed", sans-serif; letter-spacing: -1px;
  }
  .call-button svg { width: 38px; height: 38px; fill: var(--white); }
</style>
</head>
<body>
  <section class="billboard">
    <p class="tagline">Quality, Expertise, Durability, &amp; Storm Resistance.</p>
    <h1 class="headline">Premium Porch<br>Screening Solutions.</h1>
    <div class="brand"><span class="brand-mark"></span>Harborline Porchworks</div>
    <p class="distinction">We do not build screen porches, &amp; this distinction is an important part of our service.</p>
    <div class="porch-photo" role="img" aria-label="Screened porch with white ceiling, ceiling fans and wicker lounge chairs overlooking a lawn and pond"></div>
    <div class="call-button">
      <svg viewBox="0 0 24 24" aria-hidden="true"><path d="M6.6 10.8a15.1 15.1 0 0 0 6.6 6.6l2.2-2.2a1 1 0 0 1 1-.25 11.4 11.4 0 0 0 3.6.57 1 1 0 0 1 1 1V20a1 1 0 0 1-1 1A17 17 0 0 1 3 4a1 1 0 0 1 1-1h3.5a1 1 0 0 1 1 1c0 1.25.2 2.45.57 3.57a1 1 0 0 1-.25 1z"/></svg>
      <span>910.555.0147</span>
    </div>
  </section>
</body>
</html>
```